PillPeak website blog. Simple medical advice given in clear yes or no answers that save people money

I am developing a new web page that provides medical care cost savings at the consumers' fingertips. I need a web page that is clean, concise, and attractive for me to put my valuable medical information on. The information I provide is simple to obtain, yet very valuable to the consumer, and answered in a yes or no format. For example, A person may wonder if they need an antibiotic for cold like symptoms. Seeing a doctor for an antibiotic is very expensive. But with simple and clear advice at their fingertips, they can confidently avoid having to pay $200 or more to see a doctor and get an antibiotic. This is kind of like consumer reports for medical services.

Target Market(s)

People who are savvy shoppers and want to save money on healthcare. Likely younger ages between 21 and 60, who are mobile, readily use iphones, and want strong evidence based research to guide their decisions.

Industry/Entity Type

Coding

Number of Pages Required

Colors

Requirements
Must have
• A template on the "Question" and "Answer" page that can be edited many times that can be edited many times. The Confidence rating scale would need to be edited as well. The "Date Researched" the "PillPeak Pilluminate" and "References" all need to be able to be edited. This website must be very clear and simple to understand. A medical question is posed with a yes or no answer, then answered and given a confidence rating, we then tell them how much money they saved by going to our website.
Nice to have
• We want this to be slightly fun, vibrant, warm and inviting. This will be sometime later converted into an app format. Quirky, some humor to keep it interesting.
Should not have
• No sterile looking medical images. Not boring.

```html
<!DOCTYPE html>
<html lang="en">
<head>
<meta charset="utf-8">
<title>PillPeak – Clear Valuable Health Advice</title>
<link rel="stylesheet" href="https://fonts.googleapis.com/css2?family=Noto+Serif:wght@400;700&family=Roboto:wght@400;500&display=swap">
<style>
  :root {
    --red: #d7001f;
    --blue-dark: #1560b0;
    --blue-light: #2f86cf;
    --ink: #151515;
    --white: #ffffff;
    --footer: #121212;
    --arrow: #8a8f94;
  }
  * { box-sizing: border-box; margin: 0; padding: 0; }
  html, body { width: 1200px; height: 1029px; overflow: hidden; background: var(--white); }
  body { position: relative; font-family: "Roboto", sans-serif; color: var(--ink); }

  .site-header { position: absolute; top: 0; left: 0; width: 1200px; height: 161px; }
  .brand { position: absolute; left: 88px; top: 54px; display: flex; align-items: center; gap: 12px; }
  .brand-dot { width: 34px; height: 34px; border-radius: 50%; background: var(--blue-dark); }
  .brand-name { font-family: "Noto Serif", serif; font-weight: 700; font-size: 36px; color: var(--red); }
  .tagline { position: absolute; left: 331px; top: 68px; font-family: "Noto Serif", serif; font-weight: 700; font-size: 20px; letter-spacing: 0.3px; word-spacing: 6px; }
  .search { position: absolute; left: 912px; top: 56px; width: 197px; height: 46px; border: 1px solid #333; border-radius: 23px; box-shadow: 0 3px 6px rgba(0,0,0,0.12); display: flex; align-items: center; padding: 0 14px 0 16px; justify-content: space-between; font-size: 15px; color: #333; }

  .main-nav { position: absolute; top: 161px; left: 0; width: 1200px; height: 63px; background: var(--red); display: flex; align-items: center; justify-content: space-between; padding: 0 92px 0 98px; }
  .main-nav a { font-family: "Noto Serif", serif; font-size: 17px; color: var(--white); text-decoration: none; }

  .hero { position: absolute; top: 224px; left: 0; width: 1200px; height: 569px; }
  .hero-art { position: absolute; inset: 0; background:
      radial-gradient(ellipse at 82% 52%, #3aa1e6 0%, #7cc3f0 30%, rgba(200,230,250,0) 62%),
      linear-gradient(120deg, #f2f8fd 0%, #d4eaf9 40%, #a9d6f4 70%, #cfe8f8 100%); }
  .side-menu { position: absolute; left: 0; top: 61px; width: 296px; list-style: none; }
  .side-menu li { height: 65.2px; display: flex; align-items: center; justify-content: center; font-family: "Noto Serif", serif; font-size: 20px; color: var(--white); background: var(--blue-dark); border-bottom: 1px solid rgba(255,255,255,0.7); }
  .side-menu li:nth-child(even) { background: var(--blue-light); }
  .hero-copy { position: absolute; left: 342px; top: 186px; font-family: "Noto Serif", serif; font-weight: 700; text-transform: uppercase; }
  .hero-copy .big { font-size: 40px; line-height: 44px; }
  .hero-copy .line { font-size: 27px; line-height: 32px; margin-top: 20px; }
  .hero-copy .line-last { margin-top: 22px; line-height: 44px; }
  .hero-copy .line .big { font-size: 40px; }
  .slider-arrows { position: absolute; left: 346px; top: 377px; display: flex; gap: 8px; }
  .slider-arrows span { width: 25px; height: 25px; border-radius: 50%; background: var(--arrow); display: flex; align-items: center; justify-content: center; }

  .site-footer { position: absolute; top: 793px; left: 0; width: 1200px; height: 236px; background: var(--footer); color: var(--white); }
  .footer-title { position: absolute; font-family: "Noto Serif", serif; font-weight: 400; }
  .footer-title.disclaimer { left: 90px; top: 52px; font-size: 20px; }
  .footer-title.join { left: 741px; top: 50px; font-size: 24px; }
  .copyright { position: absolute; left: 90px; top: 94px; font-size: 15px; }
  .socials { position: absolute; left: 93px; top: 133px; display: flex; gap: 14px; }
  .socials span { width: 29px; height: 29px; border-radius: 50%; border: 1.5px solid var(--white); }
  .signup { position: absolute; left: 742px; top: 92px; width: 368px; height: 45px; display: flex; }
  .signup .field { flex: 1; background: var(--white); color: #333; font-size: 15px; display: flex; align-items: center; padding-left: 13px; }
  .signup .send { width: 39px; background: var(--red); display: flex; align-items: center; justify-content: center; }
  .ask { position: absolute; left: 741px; top: 153px; font-size: 16px; }
</style>
</head>
<body>
  <header class="site-header">
    <div class="brand"><span class="brand-dot"></span><span class="brand-name">PillPeak</span></div>
    <p class="tagline">CLEAR VALUABLE HEALTH ADVICE RIGHT NOW</p>
    <div class="search">
      <span>Search</span>
      <svg width="15" height="15" viewBox="0 0 16 16"><circle cx="6.5" cy="6.5" r="5" fill="none" stroke="#222" stroke-width="2.2"/><line x1="10.3" y1="10.3" x2="14.5" y2="14.5" stroke="#222" stroke-width="2.6" stroke-linecap="round"/></svg>
    </div>
  </header>

  <nav class="main-nav">
    <a href="#">PREV/SCREENING</a>
    <a href="#">WOMEN'S HEALTH</a>
    <a href="#">MEN'HEALTH</a>
    <a href="#">MEDS</a>
    <a href="#">SURGERY</a>
    <a href="#">IMAGERY</a>
    <a href="#">PEDS</a>
    <a href="#">CONTACT US</a>
  </nav>

  <section class="hero">
    <div class="hero-art" role="img" aria-label="Bright blue medical background with a glowing shield emblem"></div>
    <ul class="side-menu">
      <li>Who we are?</li>
      <li>How it works</li>
      <li>How we Know</li>
      <li>Evidence Based Research</li>
      <li>Dr.Whitlow</li>
      <li>Who we are not</li>
      <li>Are we biased?</li>
    </ul>
    <div class="hero-copy">
      <p class="big">Don't spend another</p>
      <p class="line">Clinic on your health before</p>
      <p class="line line-last">Checking us out ! <span class="big">It's free</span></p>
    </div>
    <div class="slider-arrows">
      <span><svg width="10" height="12" viewBox="0 0 10 12"><polyline points="7,1 2,6 7,11" fill="none" stroke="#fff" stroke-width="2"/></svg></span>
      <span><svg width="10" height="12" viewBox="0 0 10 12"><polyline points="3,1 8,6 3,11" fill="none" stroke="#fff" stroke-width="2"/></svg></span>
    </div>
  </section>

  <footer class="site-footer">
    <h2 class="footer-title disclaimer">Disclaimer</h2>
    <p class="copyright">© Copyright 2018 . All Rights Reserved.</p>
    <div class="socials"><span></span><span></span><span></span><span></span></div>
    <h2 class="footer-title join">Become a pillpeak today!</h2>
    <div class="signup">
      <div class="field">Enter Email</div>
      <div class="send"><svg width="18" height="18" viewBox="0 0 20 20"><path d="M19 1 L1 9 L8 11 L10 19 Z" fill="#fff"/><path d="M19 1 L8 11" stroke="#d7001f" stroke-width="1.6"/></svg></div>
    </div>
    <p class="ask">Ask a Question Here! If it is Worthy,Will post it!</p>
  </footer>
</body>
</html>
```